Maplecrest Disability - Social Security Disability Attorneys

Our company is expanding to attract clients nationwide for our social security disability practice. We have a logo, but I am looking for a creative and elegant letterhead that projects an image of being technologically advanced but still professional enough for the legal field. I am looking for the "wow factor" combined with this is still professional enough for a law practice.

Requesting letterhead and business card design
Updates

Had to update and change the logo. The previous logo had a typo. Please send updates with the new logo for consideration. The letterhead and business cards should be professional enough to be used for a law firm. Thanks.

Industry/Entity Type

Law Practice, Law Firm, Healthcare Industry, Government

Colors

Designer to choose colors to be used in the design.

Requirements
Nice to have
• **Please create a vertical design for the business card**

```html
<!DOCTYPE html>
<html lang="en">
<head>
<meta charset="utf-8">
<title>Maplecrest Disability – Business Card</title>
<link rel="stylesheet" href="https://fonts.googleapis.com/css2?family=Open+Sans:wght@400;600&display=swap">
<style>
  :root {
    --bg: #2a2c30;
    --paper: #ffffff;
    --orange: #f07a12;
    --orange-deep: #dc650a;
    --orange-light: #fb9a2e;
    --navy: #1f2a5a;
    --blue-line: #4a6af0;
    --ink: #4a4a4a;
    --muted: #9a9a9a;
  }
  * { box-sizing: border-box; margin: 0; padding: 0; }
  html, body { width: 1200px; height: 900px; overflow: hidden; background: var(--bg); }
  .canvas { position: relative; width: 1200px; height: 900px; }

  .card {
    position: absolute;
    width: 540px;
    height: 310px;
    border-radius: 26px;
    overflow: hidden;
    box-shadow: 0 14px 30px rgba(0,0,0,.45);
  }
  .card--front { left: 40px; top: 295px; background: var(--paper); }
  .card--back {
    left: 620px; top: 295px;
    background: linear-gradient(135deg, var(--orange-deep) 0%, var(--orange) 55%, var(--orange-light) 100%);
  }

  /* front */
  .brand {
    position: absolute; left: 34px; top: 40px;
    font-family: "Open Sans", sans-serif; font-weight: 600;
    font-size: 24px; letter-spacing: 0; color: var(--navy);
  }

  .rule {
    position: absolute; left: 34px; top: 104px;
    width: 440px; height: 2px; background: var(--blue-line);
  }
  .rule__end {
    position: absolute; right: -14px; top: -6px;
    width: 14px; height: 14px; background: var(--orange);
  }

  .contacts {
    position: absolute; left: 34px; top: 124px;
    list-style: none;
    font-family: "Open Sans", sans-serif; font-size: 13px; color: var(--ink);
  }
  .contacts li { display: flex; align-items: center; gap: 8px; height: 22px; }
  .contacts .icon { width: 14px; height: 14px; flex: none; }
  .contacts .gap { width: 10px; }

  .person {
    position: absolute; left: 340px; top: 206px;
    padding-left: 14px;
    border-left: 4px solid var(--orange);
    font-family: "Open Sans", sans-serif;
  }
  .person__name { font-size: 22px; color: var(--orange); line-height: 1.1; }
  .person__role { font-size: 12px; color: var(--muted); margin-top: 2px; }

  .edge-band { position: absolute; left: 0; bottom: 0; width: 100%; height: 30px; }

  /* back */
  .back-glow { position: absolute; inset: 0;
    background: radial-gradient(ellipse at 45% 45%, rgba(255,190,110,.25), rgba(255,190,110,0) 60%); }
  .back-brand {
    position: absolute; left: 0; right: 0; top: 116px; text-align: center;
    font-family: "Open Sans", sans-serif; font-weight: 600;
    font-size: 28px; color: var(--navy);
  }
  .back-web {
    position: absolute; left: 0; right: 0; top: 196px; text-align: center;
    font-family: "Open Sans", sans-serif; font-weight: 600; font-size: 15px; color: #fff;
  }
</style>
</head>
<body>
<main class="canvas">

  <section class="card card--front" aria-label="Business card front">
    <p class="brand">Maplecrest Disability</p>

    <div class="rule"><span class="rule__end"></span></div>

    <ul class="contacts">
      <li>
        <svg class="icon" viewBox="0 0 14 14"><circle cx="7" cy="7" r="7" fill="#f07a12"/><path d="M7 3.2a2.4 2.4 0 0 0-2.4 2.4C4.6 7.4 7 10.6 7 10.6s2.4-3.2 2.4-5A2.4 2.4 0 0 0 7 3.2z" fill="#fff"/><circle cx="7" cy="5.6" r=".9" fill="#f07a12"/></svg>
        Level 00, 00 Example Street, Example 0
      </li>
      <li>
        <svg class="icon" viewBox="0 0 14 14"><circle cx="7" cy="7" r="7" fill="#f07a12"/><path d="M4.3 3.6l1.5-.3.8 1.9-.9.7a5 5 0 0 0 2.4 2.4l.7-.9 1.9.8-.3 1.5c-3.4.2-6.3-2.7-6.1-6.1z" fill="#fff"/></svg>
        0000 000 129
        <span class="gap"></span>
        <svg class="icon" viewBox="0 0 14 14"><circle cx="7" cy="7" r="7" fill="#f07a12"/><path d="M4.3 3.6l1.5-.3.8 1.9-.9.7a5 5 0 0 0 2.4 2.4l.7-.9 1.9.8-.3 1.5c-3.4.2-6.3-2.7-6.1-6.1z" fill="#fff"/></svg>
        0000 000 130
      </li>
      <li>
        <svg class="icon" viewBox="0 0 14 14"><circle cx="7" cy="7" r="7" fill="#f07a12"/><rect x="3.5" y="4.5" width="7" height="5" rx=".6" fill="#fff"/><path d="M3.7 4.8L7 7.3l3.3-2.5" stroke="#f07a12" stroke-width=".8" fill="none"/></svg>
        contact@maplecrestdisability.com
      </li>
      <li>
        <svg class="icon" viewBox="0 0 14 14"><circle cx="7" cy="7" r="7" fill="#f07a12"/><circle cx="7" cy="7" r="3.6" fill="none" stroke="#fff" stroke-width=".9"/><ellipse cx="7" cy="7" rx="1.5" ry="3.6" fill="none" stroke="#fff" stroke-width=".8"/><path d="M3.4 7h7.2" stroke="#fff" stroke-width=".8"/></svg>
        www.maplecrestdisability.com
      </li>
    </ul>

    <div class="person">
      <p class="person__name">Example Name</p>
      <p class="person__role">Designation</p>
    </div>

    <svg class="edge-band" viewBox="0 0 540 30" preserveAspectRatio="none" aria-hidden="true">
      <rect x="0" y="8" width="70" height="3" fill="#f07a12"/>
      <rect x="84" y="8" width="180" height="3" fill="#4a6af0"/>
      <rect x="276" y="8" width="264" height="3" fill="#f07a12"/>
      <rect x="0" y="20" width="540" height="10" fill="#f07a12"/>
    </svg>
  </section>

  <section class="card card--back" aria-label="Business card back">
    <div class="back-glow" role="img" aria-label="Soft orange background where faint brand artwork belongs"></div>
    <p class="back-brand">Maplecrest Disability</p>
    <p class="back-web">www.maplecrestdisability.com</p>
  </section>

</main>
</body>
</html>
```